Super elegant, crisp & clean Business card design required

We recently upgraded our branding - which is on our website - talvendoraphoto.com

I would like a simple, yet elegant, clean business card design please.

The font of my logo is Cinzel - and because of the natural colour - it's best to have this on a black background.

I would like to have the back of the business card - with simply my logo.

PLEASE DO NOT SUBMIT A COMPLICATED / UNCLEAN DESIGN

Industry/Entity Type

Business

Contact Information for Business Card

Talven Doroshko Photography

Font styles to use
Other font styles liked:
• Cinzel

Requirements
Must have
• A backpage with nothing but my logo
• Simple design - stands out
Should not have
• Colour that dont align with my logo
• Over complicated '/ non symmetrical design

```html
<!DOCTYPE html>
<html lang="en">
<head>
<meta charset="utf-8">
<title>Talven Doroshko Photography – Business Card</title>
<link rel="stylesheet" href="https://fonts.googleapis.com/css2?family=Cinzel:wght@400;500&display=swap">
<style>
  :root {
    --page-bg: #2e3033;
    --card-tan: #7d6d52;
    --card-dark: #2a2b2b;
    --gold: #8c7856;
    --gold-line: #7b6a4d;
    --ink-light: #f2efe9;
    --ink-soft: #e6e2da;
  }
  * { margin: 0; padding: 0; box-sizing: border-box; }
  html, body {
    width: 1200px; height: 864px; overflow: hidden;
    background: var(--page-bg);
    font-family: "Cinzel", serif;
  }
  .sheet {
    position: relative; width: 1200px; height: 864px;
  }
  .card {
    position: absolute; left: 250px; width: 700px; height: 400px;
    box-shadow: 0 10px 30px rgba(0,0,0,0.35);
  }
  /* back of card */
  .card--back { top: 24px; background: var(--card-tan); }
  .back-brand {
    position: absolute; left: 0; right: 0; top: 230px;
    text-align: center; color: var(--ink-light);
  }
  .brand-name { font-size: 34px; font-weight: 400; letter-spacing: 1px; line-height: 1; }
  .brand-sub  { font-size: 13px; font-weight: 400; letter-spacing: 12px; margin-top: 6px; }

  /* front of card */
  .card--front { top: 440px; background: var(--card-dark); }
  .front-brand {
    position: absolute; right: 40px; top: 58px; text-align: center;
    color: var(--gold); display: flex; align-items: center; gap: 22px;
  }
  .brand-dot { width: 44px; height: 44px; border-radius: 50%; border: 1.5px solid var(--gold); }
  .front-brand .brand-name { font-size: 28px; }
  .front-brand .brand-sub { font-size: 11px; letter-spacing: 10px; margin-top: 4px; }

  .holder { position: absolute; left: 44px; top: 138px; color: var(--ink-light); }
  .holder-name { font-size: 22px; letter-spacing: 0.5px; }
  .holder-role { font-size: 14px; margin-top: 2px; color: var(--ink-soft); }

  .divider {
    position: absolute; left: 300px; right: 30px; top: 196px;
    height: 1px; background: var(--gold-line);
  }
  .contacts {
    position: absolute; right: 36px; top: 222px; list-style: none;
    text-align: right; color: var(--ink-light); font-size: 16px; line-height: 25px;
  }
  .contacts li { display: flex; justify-content: flex-end; align-items: center; gap: 8px; }
  .contacts svg { width: 12px; height: 12px; fill: var(--gold); }
  .contacts .address { margin-right: 20px; }
</style>
</head>
<body>
<main class="sheet">
  <section class="card card--back" aria-label="Card back">
    <div class="back-brand">
      <div class="brand-name">Talven Doroshko</div>
      <div class="brand-sub">PHOTOGRAPHY</div>
    </div>
  </section>

  <section class="card card--front" aria-label="Card front">
    <div class="front-brand">
      <span class="brand-dot" aria-hidden="true"></span>
      <div>
        <div class="brand-name">Talven Doroshko</div>
        <div class="brand-sub">PHOTOGRAPHY</div>
      </div>
    </div>

    <div class="holder">
      <div class="holder-name">Elias Varnholt</div>
      <div class="holder-role">Managing Director</div>
    </div>

    <div class="divider"></div>

    <ul class="contacts">
      <li>(044)-456-7890
        <svg viewBox="0 0 12 12" aria-hidden="true"><path d="M2.5 1l2 2.3-1 1.2c.7 1.5 1.6 2.4 3 3l1.2-1L10 8.5 9 10.5C5 10.2 1.8 7 1.5 3z"/></svg></li>
      <li>123-456-7890
        <svg viewBox="0 0 12 12" aria-hidden="true"><rect x="3" y="0.5" width="6" height="11" rx="1"/><rect x="4" y="2" width="4" height="6.5" fill="#2a2b2b"/></svg></li>
      <li>info@youremail.com
        <svg viewBox="0 0 12 12" aria-hidden="true"><rect x="0.5" y="2.5" width="11" height="7.5"/><path d="M0.5 2.5L6 7l5.5-4.5" fill="none" stroke="#2a2b2b" stroke-width="1"/></svg></li>
      <li>www.talvendoraphoto.com
        <svg viewBox="0 0 12 12" aria-hidden="true"><circle cx="6" cy="6" r="5.5"/><path d="M0.5 6h11M6 0.5c-3 3-3 8 0 11M6 0.5c3 3 3 8 0 11" fill="none" stroke="#2a2b2b" stroke-width="0.8"/></svg></li>
      <li class="address">12345, Address Goes Here Country Name, 123456</li>
    </ul>
  </section>
</main>
</body>
</html>
```